Velvet Harbor Snout Sticks - our own unique product line of cotton swabs

We have something now that we are not too happy with. Looking to create a label for a line of cotton swabs that we have created and designed to clean your nose from mucus and boogers. The logo that i have so far for the packaging is the white background with the black silhouette nose (attached). We need something that can do well in the retail/consumer market. Our website address (even though it is not live yet) should be listed somewhere on the label....
www.VelvetHarborGoods.example ( we sell pillows, but we have other product lines)
We would also like to see a brief description on how to correctly use the nose pick on the back side of the label. The description on how to use should read " insert cotton nose pick into nostril and give it a few counter clock wise twirls or till you feel mucus/debris latch onto the cotton. You may need to repeat the process and use more than one nose pick to achieve desired result."
As well as a warning mentioning : "Never insert plastic end of nose pick into any part of your body. Be careful and use with caution."
Also for you to know, the cotton is made from 100% natural cotton, the cotton head itself is thick and highly absorbent making it a pleasure to use. There are 50 nose picks per pack.
We're fine with keeping it simple and not making the packaging too busy, however we're open to your ideas and designs! I have given you the most important information relevant to the project. If there are any questions or something is not clear enough please kindly message me.

Requirements
Must have
• professional looking
clean looking
not busy
Should not have
• words clumping together making it appear as too much text in one area
too much text clumped together on the design

```html
<!DOCTYPE html>
<html lang="en">
<head>
<meta charset="utf-8">
<title>Velvet Harbor Snout Sticks – Cotton Swab Label</title>
<link rel="stylesheet" href="https://fonts.googleapis.com/css2?family=Ubuntu:wght@400&family=Roboto:ital,wght@1,700;1,900&display=swap">
<style>
  :root {
    --backdrop: #ebebeb;
    --teal: #1b9c8e;
    --teal-light: #2fb3a3;
    --navy: #25253a;
    --navy-soft: #2e2e46;
    --orange: #e8892b;
    --orange-deep: #e2552b;
    --red: #e0312d;
    --white: #ffffff;
  }
  html, body {
    margin: 0;
    width: 1200px;
    height: 1064px;
    overflow: hidden;
    background: var(--backdrop);
  }
  .canvas {
    position: relative;
    width: 1200px;
    height: 1064px;
  }
  .label {
    position: absolute;
    left: 150px;
    top: 212px;
    width: 900px;
    height: 640px;
    box-shadow: 0 18px 40px rgba(0,0,0,0.12);
  }
  .brand-name {
    font-family: "Ubuntu", sans-serif;
    font-weight: 400;
    fill: var(--white);
  }
  .product-title {
    font-family: "Roboto", sans-serif;
    font-style: italic;
    font-weight: 900;
    fill: var(--white);
  }
  .web-address {
    font-family: "Roboto", sans-serif;
    font-style: italic;
    font-weight: 700;
    fill: var(--white);
  }
</style>
</head>
<body>
<main class="canvas">
  <svg class="label" viewBox="0 0 900 640" xmlns="http://www.w3.org/2000/svg" aria-label="Velvet Harbor Snout Sticks cotton swab label">
    <defs>
      <linearGradient id="orangeBand" x1="0" y1="0" x2="1" y2="1">
        <stop offset="0" stop-color="var(--orange)"/>
        <stop offset="1" stop-color="var(--orange-deep)"/>
      </linearGradient>
      <linearGradient id="redStripe" x1="0" y1="1" x2="1" y2="0">
        <stop offset="0" stop-color="var(--orange-deep)"/>
        <stop offset="1" stop-color="var(--red)"/>
      </linearGradient>
    </defs>

    <rect class="label-base" width="900" height="640" fill="var(--teal)"/>

    <path class="accent-band" d="M0,0 L70,0 L470,360 L0,150 Z" fill="url(#orangeBand)"/>

    <path class="red-stripe" d="M300,640 C520,600 760,520 900,420 L900,470 C760,560 560,620 420,640 Z" fill="url(#redStripe)"/>

    <path class="wave-edge" d="M0,140 C200,200 340,330 470,370 C610,410 780,320 900,270" fill="none" stroke="var(--white)" stroke-width="14"/>

    <path class="navy-wave" d="M0,140 C200,200 340,330 470,370 C610,410 780,320 900,270 L900,420 C760,520 520,600 300,640 L0,640 Z" fill="var(--navy)"/>

    <rect class="nose-artwork" role="img" aria-label="Nose silhouette line illustration" x="60" y="280" width="220" height="300" rx="18" fill="var(--navy-soft)"/>

    <g class="brand-lockup" transform="translate(470 210) rotate(-12)">
      <circle cx="0" cy="-14" r="10" fill="var(--white)"/>
      <text class="brand-name" x="24" y="0" font-size="50">Velvet Harbor</text>
      <text class="brand-name" x="26" y="52" font-size="30" letter-spacing="6">Snout Sticks</text>
    </g>

    <g class="product-title-block" transform="translate(320 500) rotate(-8)">
      <text class="product-title" x="20" y="0" font-size="44">COTTON</text>
      <text class="product-title" x="0" y="70" font-size="76">SWABS</text>
    </g>

    <text class="web-address" font-size="20" transform="translate(560 615) rotate(-16)">www.VelvetHarborGoods.example</text>
  </svg>
</main>
</body>
</html>
```